cafe marlowpin breakfast lunch dinner menu

I am launching my new menu on the 1st of feb and i need a new menu design asap.

This is our logo that we want on the front page

our cafe is industral rustic however we have trees inside everything is timber inside. quite allot of green plants flowers everyhwere.

these photos should give you a understanding of what my cafe looks like and offers
Thanks

Target Market(s)

cafe

Industry/Entity Type

Cafe

Font styles to use
Sans Serif

Colors
85cae6
000000
ffffff
abd036

Requirements
Must have
• 2 pictures of food
Nice to have
• facebook instgram logo on the bottom so people can know we are on these platforms.

```html
<!DOCTYPE html>
<html lang="en">
<head>
<meta charset="utf-8">
<title>Cafe Marlowpin Menu</title>
<link rel="stylesheet" href="https://fonts.googleapis.com/css2?family=Bree+Serif&family=Gochi+Hand&display=swap">
<style>
  :root {
    --board: #393939;
    --board-dark: #2c2c2c;
    --board-light: #454545;
    --chalk: #f4f4f4;
    --ink: #111111;
    --photo-a1: #b7a79a;
    --photo-a2: #4a3328;
    --photo-b1: #d98a3a;
    --photo-b2: #6b4a38;
    --photo-c1: #a89888;
    --photo-c2: #3f2c22;
  }
  * { margin: 0; padding: 0; box-sizing: border-box; }
  html, body { width: 848px; height: 1200px; overflow: hidden; background: var(--board-dark); }
  .menu {
    position: relative;
    width: 848px;
    height: 1200px;
    overflow: hidden;
    background:
      radial-gradient(ellipse at 30% 40%, var(--board-light) 0%, transparent 60%),
      radial-gradient(ellipse at 75% 75%, #404040 0%, transparent 55%),
      linear-gradient(180deg, var(--board) 0%, var(--board-dark) 100%);
  }
  .photo-strip { position: absolute; top: 0; left: 0; width: 848px; height: 272px; display: flex; }
  .photo { height: 272px; }
  .photo--pancakes { width: 288px; background: linear-gradient(160deg, var(--photo-a1), var(--photo-a2)); }
  .photo--roll { width: 286px; background: linear-gradient(150deg, var(--photo-b1), var(--photo-b2)); }
  .photo--stack { width: 274px; background: linear-gradient(200deg, var(--photo-c1), var(--photo-c2)); }
  .divider { position: absolute; left: 424px; top: 302px; width: 5px; height: 786px; background: var(--chalk); }
  .item-title {
    position: absolute;
    width: 252px;
    height: 72px;
    transform: translateX(-50%);
  }
  .item-title svg { position: absolute; inset: 0; width: 100%; height: 100%; }
  .item-title span {
    position: relative;
    display: block;
    line-height: 72px;
    text-align: center;
    font-family: "Bree Serif", Georgia, serif;
    font-weight: 700;
    font-size: 26px;
    color: var(--ink);
    letter-spacing: -0.2px;
  }
  .item-desc, .item-price {
    position: absolute;
    transform: translateX(-50%);
    text-align: center;
    white-space: nowrap;
    color: var(--chalk);
    font-family: "Gochi Hand", "Comic Sans MS", cursive;
  }
  .item-desc { font-size: 18px; line-height: 24px; }
  .item-price { font-size: 34px; line-height: 40px; }
</style>
</head>
<body>
<div class="menu">
  <svg width="0" height="0" style="position:absolute">
    <defs>
      <symbol id="brush-banner" viewBox="0 0 252 72" preserveAspectRatio="none">
        <path fill="#ffffff" d="M14 10 L30 6 L44 9 L60 4 L80 8 L100 3 L122 7 L140 2 L162 7 L184 3 L204 8 L222 4 L238 9 L244 6 L240 18 L248 24 L242 32 L250 40 L244 48 L249 56 L238 60 L244 68 L226 64 L208 69 L186 65 L166 70 L144 66 L122 70 L100 65 L80 70 L58 66 L38 70 L20 65 L8 68 L12 58 L2 52 L10 44 L4 36 L12 30 L6 22 L12 16 Z"/>
      </symbol>
    </defs>
  </svg>

  <div class="photo-strip">
    <div class="photo photo--pancakes" role="img" aria-label="Stacked pancakes with chocolate, ice cream and fairy floss"></div>
    <div class="photo photo--roll" role="img" aria-label="Bacon and egg roll beside a coffee cup"></div>
    <div class="photo photo--stack" role="img" aria-label="Chocolate pancake stack topped with ice cream"></div>
  </div>

  <div class="divider"></div>

  <!-- Left column -->
  <div class="item-title" style="left:216px; top:368px;"><svg><use href="#brush-banner"/></svg><span>BACON &amp; Egg Roll</span></div>
  <div class="item-desc" style="left:216px; top:452px;">orem ipsum dolor sit amet,<br>consectetuer adipiscing elit.<br>Aenean commodo ligula eget<br>dolor. Aenean massa. Cum<br>sociis natoque</div>
  <div class="item-price" style="left:212px; top:576px;">$7.50</div>

  <div class="item-title" style="left:216px; top:634px;"><svg><use href="#brush-banner"/></svg><span>BACON &amp; Egg Roll</span></div>
  <div class="item-desc" style="left:212px; top:718px;">orem ipsum dolor sit amet, consectetuer<br>adipiscing elit.<br>Aenean commodo ligula eget</div>
  <div class="item-price" style="left:212px; top:786px;">$3.50</div>

  <div class="item-title" style="left:216px; top:860px;"><svg><use href="#brush-banner"/></svg><span>BACON &amp; Egg Roll</span></div>
  <div class="item-desc" style="left:212px; top:954px;">Corn Tortillas<br>orem ipsum dolor sit amet,<br>consectetuer adipiscing elit.<br>Aenean commodo ligula eget</div>
  <div class="item-price" style="left:194px; top:1064px;">$3.50</div>

  <!-- Right column -->
  <div class="item-title" style="left:632px; top:368px;"><svg><use href="#brush-banner"/></svg><span>BACON &amp; Egg Roll</span></div>
  <div class="item-desc" style="left:636px; top:474px;">orem ipsum dolor sit amet,<br>consectetuer adipiscing elit.<br>Aenean commodo ligula eget</div>
  <div class="item-price" style="left:634px; top:550px;">$6</div>

  <div class="item-title" style="left:632px; top:634px;"><svg><use href="#brush-banner"/></svg><span>BACON &amp; Egg Roll</span></div>
  <div class="item-desc" style="left:636px; top:718px;">(we love our city)<br>orem ipsum dolor sit amet,<br>consectetuer adipiscing elit.<br>Aenean commodo ligula eget</div>
  <div class="item-price" style="left:634px; top:818px;">$6</div>

  <div class="item-title" style="left:632px; top:860px;"><svg><use href="#brush-banner"/></svg><span>BACON &amp; Egg Roll</span></div>
  <div class="item-desc" style="left:636px; top:944px;">(Kosher &amp; Halal)<br>orem ipsum dolor sit amet,<br>consectetuer adipiscing elit.<br>Aenean commodo ligula eget</div>
  <div class="item-price" style="left:618px; top:1068px;">$6</div>
</div>
</body>
</html>
```